New Book and ebook Cover Design healing holistic/integrative cancer Project

Creation of an Ebook + Book format A5. about cure of Cancer.

Guide d'aide à la guérison

Under title Développez vos capacités de "guérisseur intérieur"
Créez votre résiliance, transmutez votre maladie en cadeaux de la vie.
Develop your self healer skills: Create your resilience, transmute your illness into gifts of life.

The 3 mains idea for the book:
- A symbolic with the icone pink of cancer with french word around (like: amour, aide, guérison, holistique, âme, corps, esprit, divin, vie):
The main target is people with cancer
Image of cancer icon ot with a tree;
- Create a Healing Journey ( image included or another idea)
- A tranversal integrative (global health soul body spirit )Journey Trough :
Spirituality, the psychoemotionnel understanding of the disease, the benefits of row ecologic foods, the medecines of the word, (Ayurveda, Chinese, Shamanism), quantum medicine, energy healing,+16 auto techniques self care
So you can illustrate the main parcours with image or icon about it
readers must feel the love the main what this book can bring them as gifts

Additionnal icon :
l’icône Leafward Pledge blue can be added. Promesse Leafward

Target Market(s)

people with cancer, professionnel of healing in integrative issue

Industry/Entity Type

Health And Wellness

Other font styles liked:
• arial colibri

Colors
abd037
e667a6
a64599

Requirements
Must have
• The 3 mains idea for the book:
• - A symbolic with the icone pink of cancer with french word around (like: amour, aide, guérison, holistique, âme, corps, esprit, divin, vie):
• The main target is people with cancer
• Image of cancer icon ot with a tree;
• - Create a Healing Journey ( image included or another idea)
• - A tranversal integrative (global health soul body spirit )Journey Trough :
• Spirituality, the psychoemotionnel understanding of the disease, the benefits of row ecologic foods, the medecines of the word, (Ayurveda, Chinese, Shamanism), quantum medicine, energy healing,+16 auto techniques self care
• So you can illustrate the main parcours with image or icon about it
• readers must feel the love the main what this book can bring them as gifts
• If you don't put icone or image for the benefits about the book:
• cloud of words in cancer symbol (and replace love words by this list)
• Parcours de Guérisons : Create a Healing Journey
• Médecine Intégrative -Santé Intégrative (âme-corps-esprit) (Soul-Body-Spirit)
• Médecine du Monde (Ayurveda, Médecine Chinoise, Chamanisme) ( Ayurveda, Chinese Médicine, Shamanism)
• Alimentation vibrante ( vibrant raw food)
• Energies de guérison
• Plus de 20 Techniques d’auto-soins
Nice to have
• 1/idea of ​​backgrounds with orbs in violet color (the fine notion of connection to the universe to the divine is to be passed on in this book)
• 2/ People can Create their own Healing Journey '( image for healing journey with roads for exemple)
• 3/ cancer symbole with words around spirit of the book french word around (like: amour, aide, guérison, holistique, âme, corps, esprit, divin, vie):
• pink/magenta and green color
• 4/ idea of gift with love?
• 5/ Lucien Marvaux ( Name of autor)
• The goal is you can live, it's possible!
Should not have
• put to much information keep focuse on the spirit of the book. People in less 30 second will be interest for buy and USED this book
• use the same type of the same type of font

```html
<!DOCTYPE html>
<html lang="fr">
<head>
<meta charset="utf-8">
<title>Quatrième de couverture – Guide d'aide à la guérison</title>
<link href="https://fonts.googleapis.com/css2?family=Hind:wght@400;500&display=swap" rel="stylesheet">
<style>
  :root {
    --bg-green: #96b976;
    --title-green: #5b7f2c;
    --ink: #1c1c1c;
    --panel: #c5c885;
    --panel-shadow: #a8bd7c;
    --rule: #6f8a52;
    --photo-bg: #e9ebef;
    --photo-suit: #2b3550;
  }
  * { margin: 0; padding: 0; box-sizing: border-box; }
  html, body { width: 880px; height: 1200px; overflow: hidden; }
  body {
    background: var(--bg-green);
    font-family: "Hind", "Segoe UI", sans-serif;
    color: var(--ink);
    position: relative;
  }
  .emblem {
    position: absolute;
    left: 240px; top: 0;
    width: 400px; height: 280px;
  }
  .headline {
    position: absolute;
    top: 286px; left: 60px; width: 760px;
    text-align: center;
    color: var(--title-green);
    font-weight: 500;
    font-size: 22.5px;
    line-height: 24px;
    text-transform: uppercase;
    letter-spacing: 0.1px;
  }
  .blurb {
    position: absolute;
    left: 96px; width: 686px;
    font-size: 17.3px;
    line-height: 23.7px;
    text-align: justify;
  }
  .blurb-intro { top: 368px; }
  .blurb-path { top: 439px; }
  .blurb-tools { top: 582px; }
  .divider {
    position: absolute;
    left: 152px; top: 760px;
    width: 574px; height: 1px;
    background: var(--rule);
  }
  .author-shadow {
    position: absolute;
    left: 74px; top: 814px;
    width: 718px; height: 260px;
    background: var(--panel-shadow);
  }
  .author-panel {
    position: absolute;
    left: 83px; top: 804px;
    width: 720px; height: 260px;
    background: var(--panel);
  }
  .author-photo {
    position: absolute;
    left: 20px; top: 19px;
    width: 179px; height: 220px;
    background: linear-gradient(180deg, var(--photo-bg) 0%, var(--photo-bg) 55%, var(--photo-suit) 100%);
  }
  .author-bio {
    position: absolute;
    left: 231px; top: 33px;
    width: 468px;
    font-size: 13.7px;
    line-height: 21.8px;
    text-align: justify;
  }
</style>
</head>
<body>

  <svg class="emblem" viewBox="0 0 400 280" role="img" aria-label="Emblème lumineux de la fleur de vie rayonnant sur fond vert">
    <defs>
      <radialGradient id="glow" cx="50%" cy="50%" r="50%">
        <stop offset="0%" stop-color="#e8f7d0" stop-opacity="0.95"/>
        <stop offset="35%" stop-color="#cfe58a" stop-opacity="0.75"/>
        <stop offset="70%" stop-color="#b2cf78" stop-opacity="0.35"/>
        <stop offset="100%" stop-color="#96b976" stop-opacity="0"/>
      </radialGradient>
    </defs>
    <circle cx="200" cy="136" r="140" fill="url(#glow)"/>
    <circle cx="200" cy="136" r="104" fill="none" stroke="#9a7a4c" stroke-width="1.5" opacity="0.8"/>
  </svg>

  <h1 class="headline">Et si votre maladie n’était autre que l’appel de votre<br>âme à retrouver votre essence véritable ?</h1>

  <p class="blurb blurb-intro">Cet ouvrage est une invitation à entreprendre l’alchimie en vous grâce à l’Amour.</p>

  <p class="blurb blurb-path">Un chemin de guérison est et reste plus que jamais possible. Emprunt de sagesse divine, la spiritualité est décryptée avec simplicité en y associant une compréhension globale de l’être âme corps esprit dans un recouvrement intégratif de la guérison. Vous y découvrirez une mine d’informations utiles pour vous aider à transmuter votre plomb en or.</p>

  <p class="blurb blurb-tools">Concentré d’outils tant Ancestraux que modernes allant de l’Alimentation Saine Vivante et Vibrante à la Respiration Consciente, en passant par l’Aromathérapie, l’EFT, l’Auto-hypnose Humaniste, la Lithothérapie, la Réflexologie Plantaire… ainsi que les Médecines millénaires du monde, sans oublier les possibilités offertes par les thérapies quantiques dans une dimension énergétique multidimensionnelle de l’être.</p>

  <div class="divider"></div>

  <div class="author-shadow"></div>
  <section class="author-panel">
    <div class="author-photo" role="img" aria-label="Portrait de l’auteur en veste sombre et chemise claire"></div>
    <p class="author-bio">LUCIEN MARVAUX, formé à la santé de l’Habitat avec le Feng Shui Traditionnel Chinois et la Géobiologie et différents outils de santé holistique allant de l’Aromathérapie aux Thérapies Quantiques, vous présente cet ouvrage avec plaisir. L’écriture de ce livre lui est apparue comme un appel du cœur désireux d’apporter une aide significative pour prévenir, traiter le cancer ou toute autre maladie différemment sous un angle intégratif âme-corps-esprit, sans rejeter la médecine conventionnelle, mais l’inclure dans une réalité plus vaste.</p>
  </section>

</body>
</html>
```